Heron Dusk business card design

I make handmade colourful women's beaded jewellery (necklaces and earnings).
I require a business card to be designed to truly reflect my jewellery, that is, it is different and stands out.
I would like the business card to look creative, arty, gentle and feminine and fit in with the look of my website and logo (already developed).
I would like the business card to have strong use of the water reeds that are flowing in the wind (please see the banner image on my website www.herondusk.net and attached files).

Target Market(s)

Women who are fashion conscious, hip and funky. My audience like things that are a little different and stand out in a crowd.These women are aged in their 20's-40's.

Industry/Entity Type

Jewelry

Contact Information for Business Card

Please include the following items:
1) my logo: Heron Dusk
2) my name, address and phone number: Darla Fontenot, Sydney, Australia, 0498 315 270
3) my web details: www.herondusk.net, info@herondusk.net, www.facebook.com/herondusk

Font styles to use
Other font styles liked:
• Remachine Script

Requirements
Must have
• My business card must have the following:
• 1) my personal details including all my website contacts (see above).
• 2) Heron Dusk logo
• 3) Reeds flowing in the wind (see my banner image on my website www.herondusk.net or see attached files).
Nice to have
• A sunrise in the background (rising over water)
• I would prefer that the colour scheme to fit with the Heron Dusk logo, that is the colours of an early morning sunrise i.e yellows, oranges. The use of black and white is fine.
Should not have
• I do not like a commercial manufactured look with hard edges. I would like a look that is soft and reflects an artistic, creative and independent business.

```html
<!DOCTYPE html>
<html lang="en">
<head>
<meta charset="utf-8">
<title>Heron Dusk – Business Card</title>
<link rel="stylesheet" href="https://fonts.googleapis.com/css2?family=Arimo:wght@400;700&display=swap">
<style>
  :root {
    --stage: #e9e7e4;
    --card-white: #ffffff;
    --card-dark: #2b2729;
    --sun-yellow: #f7b21c;
    --sun-orange: #f08a1d;
    --ink: #1f1c1d;
    --text-light: #f2f0ee;
    --rule-grey: #9a9a9a;
    --dot-grey: #b9b4ae;
  }
  * { box-sizing: border-box; margin: 0; padding: 0; }
  html, body {
    width: 1200px; height: 950px; overflow: hidden;
    background: var(--stage);
    font-family: "Arimo", Arial, sans-serif;
  }
  .stage { position: relative; width: 1200px; height: 950px; }

  .card {
    position: absolute; left: 250px; width: 700px; height: 400px;
    background: var(--card-white);
    box-shadow: 0 6px 18px rgba(0,0,0,.18);
    overflow: hidden;
  }
  .card--front { top: 50px; }
  .card--back { top: 500px; display: flex; }

  /* brand lockup */
  .brand { display: flex; flex-direction: column; align-items: center; }
  .brand__sun {
    width: 120px; height: 120px; border-radius: 50%;
    background: var(--sun-yellow);
    border: 3px solid var(--ink);
  }
  .brand__name {
    margin-top: 14px;
    font-size: 34px; font-weight: 400; color: var(--ink);
    letter-spacing: 1px;
  }

  .card--front .brand { position: absolute; top: 70px; left: 0; right: 0; }

  .social-rule {
    position: absolute; left: 110px; right: 110px; top: 318px; height: 2px;
    background: linear-gradient(90deg, transparent, var(--rule-grey) 25%, var(--rule-grey) 75%, transparent);
  }
  .social-dots {
    position: absolute; top: 306px; left: 0; right: 0;
    display: flex; justify-content: center; gap: 8px;
  }
  .social-dots span {
    width: 24px; height: 24px; border-radius: 50%;
    background: var(--dot-grey); border: 2px solid var(--card-white);
  }

  /* back */
  .details {
    width: 300px; height: 100%;
    background: var(--card-dark);
    border-right: 3px solid var(--sun-yellow);
    color: var(--text-light);
    padding: 48px 0 0 44px;
  }
  .details__name { color: var(--sun-yellow); font-weight: 700; font-size: 24px; }
  .details__role { font-size: 17px; margin-top: 4px; }
  .details__address { margin-top: 52px; font-size: 17px; line-height: 24px; }
  .contact-list { list-style: none; margin-top: 4px; font-size: 17px; line-height: 26px; }
  .contact-list li { display: flex; align-items: center; gap: 10px; }
  .contact-list svg { width: 16px; height: 16px; flex: none; }
  .square-mark { width: 15px; height: 15px; background: var(--sun-yellow); flex: none; }

  .card--back .brand-side {
    flex: 1; display: flex; align-items: center; justify-content: center;
  }
  .card--back .brand__sun { width: 150px; height: 150px; }
  .card--back .brand__name { font-size: 40px; }
</style>
</head>
<body>
<main class="stage">

  <section class="card card--front" aria-label="Card front">
    <div class="brand">
      <div class="brand__sun"></div>
      <div class="brand__name">Heron Dusk</div>
    </div>
    <div class="social-rule"></div>
    <div class="social-dots" aria-label="Social links">
      <span></span><span></span><span></span><span></span>
    </div>
  </section>

  <section class="card card--back" aria-label="Card back">
    <div class="details">
      <p class="details__name">Tobin Hale</p>
      <p class="details__role">President</p>
      <p class="details__address">Darla Fontenot<br>Sydney, Australia</p>
      <ul class="contact-list">
        <li>
          <svg viewBox="0 0 16 16" aria-hidden="true"><path fill="#f7b21c" d="M3 1h3l1.5 4-2 1.3a9 9 0 0 0 4.2 4.2L11 8.5l4 1.5v3a2 2 0 0 1-2 2C7 15 1 9 1 3a2 2 0 0 1 2-2z"/></svg>
          0498 315 270
        </li>
        <li>
          <svg viewBox="0 0 16 16" aria-hidden="true"><rect x="1" y="3" width="14" height="10" rx="1" fill="#f7b21c"/><path d="M1.5 3.5 8 9l6.5-5.5" fill="none" stroke="#2b2729" stroke-width="1.4"/></svg>
          info@herondusk.net
        </li>
        <li>
          <svg viewBox="0 0 16 16" aria-hidden="true"><circle cx="8" cy="8" r="6.5" fill="none" stroke="#f7b21c" stroke-width="1.6"/><ellipse cx="8" cy="8" rx="2.6" ry="6.5" fill="none" stroke="#f7b21c" stroke-width="1.2"/><path d="M1.5 8h13" stroke="#f7b21c" stroke-width="1.2"/></svg>
          www.herondusk.net
        </li>
        <li>
          <span class="square-mark"></span>
          herondusk
        </li>
      </ul>
    </div>
    <div class="brand-side">
      <div class="brand">
        <div class="brand__sun"></div>
        <div class="brand__name">Heron Dusk</div>
      </div>
    </div>
  </section>

</main>
</body>
</html>
```